Business Card Design Project

Business Card
We are rebranding with a new logo
Industry/Entity Type
Business
Contact Information for Business Card
Dennis Morvale +61 487215963 dennis@quorv.com.au P.O. Box 872 Fernlow QLD 4309
Requirements
Must have
- Logo

```html
<!DOCTYPE html>
<html lang="en">
<head>
<meta charset="utf-8">
<title>Quorv International Business Card</title>
<link href="https://fonts.googleapis.com/css2?family=Roboto:wght@400;700&family=Yellowtail&display=swap" rel="stylesheet">
<style>
  :root {
    --bg: #e6e6e6;
    --blue-deep: #00557a;
    --blue-mid: #0479ad;
    --blue-bright: #02a0dc;
    --white: #ffffff;
    --paper: #f1f1f1;
    --ink: #1e2a33;
  }
  * { margin: 0; padding: 0; box-sizing: border-box; }
  html, body { width: 1200px; height: 576px; overflow: hidden; }
  body {
    background: var(--bg);
    font-family: "Roboto", Arial, sans-serif;
    position: relative;
  }
  .card {
    position: absolute;
    border-radius: 12px;
    overflow: hidden;
    box-shadow: 0 3px 6px rgba(0,0,0,0.22);
  }
  .card-front {
    left: 82px; top: 139px; width: 485px; height: 291px;
    background: linear-gradient(90deg, var(--blue-deep) 0%, var(--blue-mid) 50%, var(--blue-bright) 100%);
  }
  .card-back {
    left: 602px; top: 138px; width: 481px; height: 290px;
    background: var(--paper);
  }
  .card-back .panel { position: absolute; inset: 0; }
  .brand {
    position: absolute;
    text-align: center;
    font-weight: 700;
    letter-spacing: 2px;
    line-height: 1.15;
    display: flex; flex-direction: column; align-items: center; gap: 10px;
  }
  .brand .dot { width: 14px; height: 14px; border-radius: 50%; }
  .card-front .brand { left: 0; right: 0; top: 100px; color: var(--white); font-size: 26px; }
  .card-front .brand .dot { background: var(--white); }
  .card-back .brand { left: 262px; right: 0; top: 105px; color: var(--ink); font-size: 22px; }
  .card-back .brand .dot { background: var(--ink); }
  .holder { position: absolute; left: 22px; top: 38px; color: var(--white); }
  .holder-name { font-family: "Yellowtail", cursive; font-size: 26px; font-weight: 400; }
  .holder-title { font-size: 12px; margin-top: 2px; }
  .contact { position: absolute; left: 26px; top: 216px; list-style: none; color: var(--white); font-size: 12.5px; }
  .contact li { display: flex; align-items: center; gap: 8px; height: 17px; }
  .contact svg { width: 11px; height: 11px; fill: var(--white); }
</style>
</head>
<body>
  <div class="card card-front">
    <div class="brand"><span class="dot"></span><span>QUORV<br>INTERNATIONAL</span></div>
  </div>

  <div class="card card-back">
    <svg class="panel" width="481" height="290" viewBox="0 0 481 290">
      <defs>
        <linearGradient id="backBlue" x1="0" x2="1" y1="0" y2="0">
          <stop offset="0" stop-color="#00557a"/>
          <stop offset="1" stop-color="#0479ad"/>
        </linearGradient>
      </defs>
      <path d="M0 0 H280 Q230 145 280 290 H0 Z" fill="url(#backBlue)"/>
    </svg>
    <div class="holder">
      <p class="holder-name">Dennis Morvale</p>
      <p class="holder-title">Managing Director</p>
    </div>
    <ul class="contact">
      <li><svg viewBox="0 0 24 24"><path d="M6.6 10.8a15 15 0 0 0 6.6 6.6l2.2-2.2a1 1 0 0 1 1-.25 11.4 11.4 0 0 0 3.6.57 1 1 0 0 1 1 1V20a1 1 0 0 1-1 1A17 17 0 0 1 3 4a1 1 0 0 1 1-1h3.5a1 1 0 0 1 1 1c0 1.25.2 2.45.57 3.57a1 1 0 0 1-.25 1z"/></svg>+61 487215963</li>
      <li><svg viewBox="0 0 24 24"><path d="M2 5h20v14H2z M3.5 6.5 12 13l8.5-6.5" fill="none" stroke="#fff" stroke-width="2"/></svg>dennis@quorv.com.au</li>
      <li><svg viewBox="0 0 24 24"><path d="M12 2a7 7 0 0 0-7 7c0 5 7 13 7 13s7-8 7-13a7 7 0 0 0-7-7zm0 9.5A2.5 2.5 0 1 1 12 6.5a2.5 2.5 0 0 1 0 5z"/></svg>P.O. Box 872 Fernlow QLD 4309</li>
    </ul>
    <div class="brand"><span class="dot"></span><span>QUORV<br>INTERNATIONAL</span></div>
  </div>
</body>
</html>
```